SaaS Early tech startup business card design

Unique design for experience ecommerce platform company. the business cards will be used by executive members. conformance with color code is required.

```html
<!DOCTYPE html>
<html lang="en">
<head>
<meta charset="utf-8">
<title>Velno Business Card</title>
<link rel="stylesheet" href="https://fonts.googleapis.com/css2?family=Roboto:wght@400;500;700&display=swap">
<style>
  :root {
    --bg: #999999;
    --white: #ffffff;
    --ink: #242424;
    --blue: #0d6a92;
    --green: #0bb08f;
    --stripe-1: #0a5d8c;
    --stripe-2: #0c6b96;
    --stripe-3: #1183a3;
    --stripe-4: #0a9a94;
    --stripe-5: #10ad95;
    --stripe-6: #2fd6b3;
    --grad-top: #02c2ae;
    --grad-bottom: #05608c;
    --light: #f2f2f2;
  }
  * { margin: 0; padding: 0; box-sizing: border-box; }
  html, body { width: 1200px; height: 1200px; overflow: hidden; }
  body {
    background: var(--bg);
    font-family: "Roboto", Arial, sans-serif;
    position: relative;
  }
  .card {
    position: absolute;
    left: 262px;
    width: 686px;
    height: 392px;
    overflow: hidden;
  }
  .card--front { top: 165px; background: var(--white); }
  .card--back {
    top: 653px;
    background: linear-gradient(to bottom, var(--grad-top), var(--grad-bottom));
  }
  .wordmark {
    position: absolute;
    left: 0; right: 0;
    text-align: center;
    font-weight: 700;
    font-size: 112px;
    line-height: 1;
    letter-spacing: -2px;
  }
  .card--front .wordmark { top: 232px; top: 60px; color: var(--blue); }
  .card--back .wordmark { top: 127px; font-size: 130px; color: var(--white); }
  .stripe {
    position: absolute;
    top: 251px;
    left: 0;
    width: 100%;
    height: 7px;
    display: flex;
  }
  .stripe span { flex: 1; }
  .stripe span:nth-child(1) { background: var(--stripe-1); }
  .stripe span:nth-child(2) { background: var(--stripe-2); }
  .stripe span:nth-child(3) { background: var(--stripe-3); }
  .stripe span:nth-child(4) { background: var(--stripe-4); }
  .stripe span:nth-child(5) { background: var(--stripe-5); }
  .stripe span:nth-child(6) { background: var(--stripe-6); }
  .details {
    position: absolute;
    top: 258px;
    left: 0;
    width: 100%;
    height: 134px;
    background: var(--ink);
    color: var(--light);
  }
  .person {
    position: absolute;
    left: 39px;
    top: 25px;
  }
  .person__name {
    color: var(--blue);
    font-weight: 500;
    font-size: 23px;
    line-height: 25px;
    letter-spacing: 0.2px;
  }
  .person__role {
    color: var(--green);
    font-weight: 500;
    font-size: 16px;
    line-height: 20px;
    margin-bottom: 3px;
  }
  .person__address {
    font-size: 16px;
    line-height: 19px;
    font-style: normal;
  }
  .contacts {
    position: absolute;
    right: 38px;
    top: 40px;
    list-style: none;
    text-align: right;
    font-size: 15.5px;
    line-height: 19.6px;
  }
  .contacts li { display: flex; align-items: center; justify-content: flex-end; }
  .contacts svg { width: 13px; height: 13px; margin-left: 8px; fill: var(--green); }
</style>
</head>
<body>
  <section class="card card--front">
    <div class="wordmark">velno</div>
    <div class="stripe"><span></span><span></span><span></span><span></span><span></span><span></span></div>
    <div class="details">
      <div class="person">
        <div class="person__name">DANIEL REYES</div>
        <div class="person__role">President</div>
        <address class="person__address">2140 Harbor View Road<br>Juneau, Alaska 99801</address>
      </div>
      <ul class="contacts">
        <li>555-014-2210
          <svg viewBox="0 0 16 16"><path d="M3.5 1 6 3.8 4.8 5.6c.9 2 2.6 3.7 4.6 4.6l1.8-1.2L14 11.5 12.4 14C6.5 13.6 2.4 9.5 2 3.6z"/></svg>
        </li>
        <li>555-018-7734
          <svg viewBox="0 0 16 16"><path d="M4 0h8a1 1 0 0 1 1 1v14a1 1 0 0 1-1 1H4a1 1 0 0 1-1-1V1a1 1 0 0 1 1-1zm1 2v11h6V2z"/></svg>
        </li>
        <li>hello@velno.com
          <svg viewBox="0 0 16 16"><path d="M1 4h14v9H1zm1 1.2v.4l6 3.6 6-3.6v-.4z"/></svg>
        </li>
        <li>www.velno.com
          <svg viewBox="0 0 16 16"><circle cx="8" cy="8" r="7"/></svg>
        </li>
      </ul>
    </div>
  </section>

  <section class="card card--back">
    <div class="wordmark">velno</div>
  </section>
</body>
</html>
```